Nanny Share Ecommerce Website for Finding Childcare and Parents who need Childcare BrightPramHub.net

Our company needs an ecommerce website (BrightPramHub.net) for a US subscription based service strictly for nanny sharing that connects families and caregivers. The website would allow families to connect with one another as well as to search for nannies. The service would be searchable for other families by location (by radius or zip code), children demographic (age range/gender/special needs), days of week or times, after school care, school closure days (holidays), etc. The service would also be searchable for nannies based on gender, provider age range, years experience, language, hourly rate, transportation available, certification (CPR first aid), education etc. The search fields would be searchable and sortable and allow to connect with the provider (after paying subscription fee). The service would be similar to tendlyfolk.net in that it would allow for families and caregivers to post photos as well as a short bio of the themselves. There would also be a feedback/star rating mechanism to rate caregivers who have performed work for families (viewable to public). The service would be free for nannies to post their bios and only a subscription based service for families to connect with other families or with caregivers (able to view bio but need service to connect). There will be a short bio on the benefits of nanny sharing (reduced cost, increased flexibility for parents, reduced illness, increased socialization with other children vs. sole nanny), as well as Q&A section with best practices.

Target Market(s)

Families, Nannies

Industry/Entity Type

Childcare

Logo Text

Bright Pram Hub

Coding

Coded - Design and coding required

Number of Pages Required

5+ page

Requirements
Must have
• Searchable (need to be able to search for families as well as nannies), responsive, functional, easy to use, add value to families and nannies. Needs to be able to collect payment for subscription.
Nice to have
• Optimized for mobile, SEO optimized

```html
<!DOCTYPE html>
<html lang="en">
<head>
<meta charset="utf-8">
<title>Bright Pram Hub – Nanny Sharing</title>
<link href="https://fonts.googleapis.com/css2?family=Poppins:ital,wght@0,300;0,400;0,500;0,600;1,400&display=swap" rel="stylesheet">
<style>
:root{
  --red:#f84b4b;
  --red-dark:#e53d3d;
  --ink:#1d1d1d;
  --text:#555;
  --muted:#8a8a8a;
  --line:#e6e6e6;
  --band:#f1f1f1;
  --white:#fff;
  --star:#f5a623;
  --black:#1f1f1f;
}
*{box-sizing:border-box;margin:0;padding:0}
html,body{width:1200px;height:3077px;overflow:hidden}
body{position:relative;font-family:"Poppins",sans-serif;color:var(--text);background:var(--white)}
a{color:inherit;text-decoration:none}
.abs{position:absolute}

/* header */
.site-header{position:absolute;left:0;top:0;width:1200px;height:78px;background:var(--white)}
.brand{position:absolute;left:162px;top:24px;font-size:19px;font-weight:500;color:var(--ink);letter-spacing:.2px}
.main-nav{position:absolute;top:31px;left:0;font-size:11px;font-weight:500;color:var(--ink)}
.main-nav a{position:absolute;white-space:nowrap}
.main-nav a.active{color:var(--red)}
.search-box{position:absolute;left:769px;top:24px;width:185px;height:31px;border:1px solid var(--line);border-radius:16px;font-size:11px;color:#aaa;padding:8px 14px}
.search-box svg{position:absolute;right:12px;top:9px}
.btn-login{position:absolute;left:972px;top:25px;width:64px;height:29px;border-radius:15px;background:var(--red);color:var(--white);font-size:11px;font-weight:500;text-align:center;line-height:29px}

/* hero */
.hero{position:absolute;left:0;top:78px;width:1200px;height:542px;background:linear-gradient(100deg,#e9e4de 0%,#d8cfc4 40%,#c8a888 68%,#a97b5e 100%)}
.hero-text{position:absolute;left:162px;top:126px;width:380px}
.hero h1{font-size:44px;font-weight:400;line-height:54px;color:var(--ink)}
.hero p{margin-top:16px;font-size:14px;line-height:25px;color:var(--ink)}
.hero-actions{position:absolute;left:162px;top:338px}
.btn-pill{display:inline-block;height:38px;line-height:38px;padding:0 30px;border-radius:19px;background:var(--red);color:var(--white);font-size:11px;font-weight:500;margin-right:4px}
.slider-dots{position:absolute;left:1143px;top:240px}
.slider-dots span{display:block;width:14px;height:14px;border-radius:50%;background:var(--white);margin-bottom:11px}

/* section titles */
.section-title{position:absolute;left:0;width:1200px;text-align:center;font-size:28px;font-weight:400;color:var(--ink)}

/* services */
.service-card{position:absolute;width:428px;height:224px;border:1px solid var(--line);background:var(--white)}
.service-photo{position:absolute;left:8px;top:8px;width:199px;height:206px}
.service-body{position:absolute;left:222px;top:22px;width:194px}
.service-body h3{font-size:17px;font-weight:400;color:var(--ink);margin-bottom:10px}
.service-body p{font-size:11px;line-height:20px;color:var(--text)}
.btn-outline{display:inline-block;margin-top:12px;height:30px;line-height:28px;padding:0 16px;border:1px solid var(--red);border-radius:15px;color:var(--red);font-size:10px}

/* reviews */
.reviews{position:absolute;left:0;top:1276px;width:1200px;height:381px;background:var(--band)}
.review{position:absolute;top:135px;width:290px}
.avatar{position:absolute;left:0;top:0;width:72px;height:72px;border-radius:50%}
.review-body{position:absolute;left:90px;top:0;width:190px}
.review-body blockquote{font-size:10.5px;line-height:20px;font-style:italic;color:var(--text)}
.q{color:var(--red);font-weight:600;font-size:14px;font-style:normal}
.stars{margin-top:8px;color:var(--star);font-size:11px;letter-spacing:1px}
.reviewer{margin-top:6px;font-size:12px;font-weight:500;color:var(--ink)}

/* benefits */
.benefits{position:absolute;left:0;top:1661px;width:1200px;height:534px;background:var(--red)}
.benefits-photo{position:absolute;left:0;top:0;width:600px;height:534px;background:linear-gradient(120deg,#f4efe9 0%,#e8d2b5 45%,#d8b08a 75%,#f7f3ee 100%)}
.benefits h2{position:absolute;left:617px;top:42px;font-size:26px;font-weight:400;color:var(--white)}
.benefit{position:absolute;left:619px;width:420px}
.benefit-icon{position:absolute;left:0;top:0;width:62px;height:62px;border:2px solid var(--white);border-radius:50%}
.benefit-icon svg{position:absolute;left:16px;top:16px}
.benefit h4{position:absolute;left:74px;top:0;font-size:14px;font-weight:400;color:var(--white);line-height:21px;width:290px}
.benefit p{position:absolute;left:74px;font-size:10px;line-height:19px;color:#ffe3e3;width:340px}

/* faq */
.faq-item{position:absolute;height:50px;width:427px;border:1px solid var(--line);border-radius:25px;background:var(--white);box-shadow:0 2px 5px rgba(0,0,0,.06);font-size:13px;color:var(--ink);line-height:48px;padding-left:22px}
.faq-item .plus{position:absolute;right:22px;top:0;color:var(--red);font-size:18px;font-weight:500}
.faq-item.open{background:var(--red);border-color:var(--red);color:var(--white)}
.faq-item.open .plus{color:var(--white)}
.faq-item.open::after{content:"";position:absolute;left:70px;bottom:-9px;border-left:9px solid transparent;border-right:9px solid transparent;border-top:9px solid var(--red)}
.faq-answer{position:absolute;left:162px;top:2510px;width:427px;height:103px;border:1px solid var(--line);border-radius:14px;box-shadow:0 2px 5px rgba(0,0,0,.06);padding:18px 22px;font-size:10.5px;line-height:21px;color:var(--text)}

/* newsletter */
.newsletter{position:absolute;left:0;top:2689px;width:1200px;height:82px;background:var(--red)}
.newsletter h3{position:absolute;left:195px;top:24px;font-size:25px;font-weight:400;color:var(--white)}
.nl-input{position:absolute;left:455px;top:20px;width:460px;height:42px;border-radius:21px 0 0 21px;background:var(--white);font-size:10px;color:#aaa;line-height:42px;padding-left:20px}
.nl-submit{position:absolute;left:903px;top:20px;width:77px;height:42px;border-radius:0 21px 21px 0;background:var(--black);color:var(--white);font-size:11px;font-weight:500;text-align:center;line-height:42px}

/* footer */
.site-footer{position:absolute;left:0;top:2771px;width:1200px;height:306px;background:var(--band)}
.footer-brand{position:absolute;left:162px;top:28px;font-size:19px;font-weight:500;color:var(--ink)}
.footer-about{position:absolute;left:162px;top:72px;width:190px;font-size:11px;line-height:25px;color:var(--text)}
.footer-col{position:absolute;top:30px}
.footer-col h5{font-size:15px;font-weight:400;color:var(--ink);margin-bottom:12px}
.footer-col li{list-style:none;font-size:11px;line-height:25px;color:var(--text)}
.footer-rule{position:absolute;left:162px;top:222px;width:876px;height:1px;background:#dcdcdc}
.social{position:absolute;left:162px;top:256px}
.social span{display:inline-block;width:22px;height:22px;border-radius:50%;background:var(--ink);margin-right:12px;vertical-align:middle}
.social svg{vertical-align:middle;margin-right:12px}
.copyright{position:absolute;right:162px;top:259px;font-size:11px;color:var(--ink)}
</style>
</head>
<body>

<header class="site-header">
  <div class="brand">Bright Pram Hub</div>
  <nav class="main-nav">
    <a class="active" style="left:367px">HOME</a>
    <a style="left:420px">ABOUT US</a>
    <a style="left:498px">SERVICES</a>
    <a style="left:572px">NEWS</a>
    <a style="left:628px">FAQ</a>
    <a style="left:687px">CONTACT</a>
  </nav>
  <div class="search-box">Search
    <svg width="12" height="12" viewBox="0 0 12 12"><circle cx="5" cy="5" r="3.8" fill="none" stroke="#999" stroke-width="1.4"/><line x1="7.8" y1="7.8" x2="11" y2="11" stroke="#999" stroke-width="1.4"/></svg>
  </div>
  <a class="btn-login">LOGIN</a>
</header>

<section class="hero" role="img" aria-label="Photo of a smiling toddler playing on the floor with a caregiver and a green ball">
  <div class="hero-text">
    <h1>Welcome to<br>Bright Pram Hub</h1>
    <p>Sed ut perspiciatis unde omnis iste natus sitlup tatem accusvSed ut perspiciatis unde omlorenisste natuser ror sit voluptatemsant.</p>
  </div>
  <div class="hero-actions">
    <a class="btn-pill">FIND CARE</a><a class="btn-pill">SEARCH FOR NANNY</a>
  </div>
  <div class="slider-dots"><span></span><span></span><span></span></div>
</section>

<h2 class="section-title" style="top:656px">Our Services</h2>

<article class="service-card" style="left:162px;top:734px">
  <div class="service-photo" role="img" aria-label="Photo of a young girl holding an adult's hand" style="background:linear-gradient(135deg,#6f9a3d,#b9c98a 55%,#e9dcc6)"></div>
  <div class="service-body"><h3>Child Care</h3><p>Sed ut perspiciatis unde omnis iste natus error sit voluptatem accusan tium doloremque laudantium, tam rem aperiam, eaque ipsa quae ilo inventore veritperiam.</p><a class="btn-outline">Read More</a></div>
</article>
<article class="service-card" style="left:610px;top:734px">
  <div class="service-photo" role="img" aria-label="Photo of a caregiver helping a smiling senior woman walk" style="background:linear-gradient(135deg,#c9d8de,#e6d8cc 55%,#b99f8d)"></div>
  <div class="service-body"><h3>Senior Care</h3><p>Sed ut perspiciatis unde omnis iste natus error sit voluptatem accusan tium doloremque laudantium, tam rem aperiam, eaque ipsa quae ilo inventore veritperiam.</p><a class="btn-outline">Read More</a></div>
</article>
<article class="service-card" style="left:162px;top:982px">
  <div class="service-photo" role="img" aria-label="Photo of an orange cat being brushed" style="background:linear-gradient(135deg,#e9e1d6,#e6a35a 50%,#c8742f)"></div>
  <div class="service-body"><h3>Pet Care</h3><p>Sed ut perspiciatis unde omnis iste natus error sit voluptatem accusan tium doloremque laudantium, tam rem aperiam, eaque ipsa quae ilo inventore veritperiam.</p><a class="btn-outline">Read More</a></div>
</article>
<article class="service-card" style="left:610px;top:982px">
  <div class="service-photo" role="img" aria-label="Photo of a home carer assisting an elderly woman in a living room" style="background:linear-gradient(135deg,#efe9e2,#d8c2ac 55%,#9e8574)"></div>
  <div class="service-body"><h3>Home Care</h3><p>Sed ut perspiciatis unde omnis iste natus error sit voluptatem accusan tium doloremque laudantium, tam rem aperiam, eaque ipsa quae ilo inventore veritperiam.</p><a class="btn-outline">Read More</a></div>
</article>

<section class="reviews">
  <h2 class="section-title" style="top:50px">Reviews</h2>
  <div class="review" style="left:162px">
    <div class="avatar" role="img" aria-label="Portrait photo of reviewer" style="background:linear-gradient(135deg,#6b4a3a,#d3a98c)"></div>
    <div class="review-body">
      <blockquote><span class="q">“</span> Sed ut perspiciatis undloe loil iste natus error sit voluptatelorm accusan tium doloremque laloud antium, tam rem aperiam, ealolq ue ipsa quae ilo inventore loreve ip eriao quae ilo inven lore iptore verrem apm. <span class="q">”</span></blockquote>
      <div class="stars">★★★★★</div><div class="reviewer">Mara Quill</div>
    </div>
  </div>
  <div class="review" style="left:472px">
    <div class="avatar" role="img" aria-label="Portrait photo of reviewer" style="background:linear-gradient(135deg,#9aa7b6,#d9c3b0)"></div>
    <div class="review-body">
      <blockquote><span class="q">“</span> Sed ut perspiciatis undloe loil iste natus error sit voluptatelorm accusan tium doloremque laloud antium, tam rem aperiam, ealolq ue ipsa quae ilo inventore loreve ip eriao quae ilo inven lore iptore verrem apm. <span class="q">”</span></blockquote>
      <div class="stars">★★★★★</div><div class="reviewer">Tobin Reyes</div>
    </div>
  </div>
  <div class="review" style="left:771px">
    <div class="avatar" role="img" aria-label="Portrait photo of reviewer" style="background:linear-gradient(135deg,#c8b9a6,#eadbc9)"></div>
    <div class="review-body">
      <blockquote><span class="q">“</span> Sed ut perspiciatis undloe loil iste natus error sit voluptatelorm accusan tium doloremque laloud antium, tam rem aperiam, ealolq ue ipsa quae ilo inventore loreve ip eriao quae ilo inven lore iptore verrem apm. <span class="q">”</span></blockquote>
      <div class="stars">★★★★★</div><div class="reviewer">Ada Lindqvist</div>
    </div>
  </div>
</section>

<section class="benefits">
  <div class="benefits-photo" role="img" aria-label="Photo of a nanny laughing with two toddlers beside a wooden toy house"></div>
  <h2>Benefits</h2>
  <div class="benefit" style="top:103px">
    <div class="benefit-icon"><svg width="28" height="28" viewBox="0 0 28 28"><text x="14" y="21" text-anchor="middle" font-family="Poppins,sans-serif" font-size="20" fill="#fff">$</text></svg></div>
    <h4>Reduced Cost</h4>
    <p style="top:24px">Sed ut perspiciatis unde omnis iste natus erronsit voluptate cuol oeut perspiciatis undeomn isstnatusevo llatan.</p>
  </div>
  <div class="benefit" style="top:189px">
    <div class="benefit-icon"><svg width="28" height="28" viewBox="0 0 28 28" fill="#fff"><circle cx="10" cy="9" r="4"/><path d="M2 22c0-5 3.5-7.5 8-7.5s8 2.5 8 7.5z"/><circle cx="19" cy="10" r="3.2"/><path d="M17 15c4 0 9 1.5 9 7h-6c0-3-1-5-3-7z"/></svg></div>
    <h4>Increased flexibility for parents</h4>
    <p style="top:24px">Sed ut perspiciatis unde omnis iste natus erronsit voluptate cuol oeut perspiciatis undeomn isstnatusevo llatan.</p>
  </div>
  <div class="benefit" style="top:275px">
    <div class="benefit-icon"><svg width="28" height="28" viewBox="0 0 28 28" fill="#fff"><rect x="3" y="14" width="4" height="10"/><rect x="9" y="10" width="4" height="14"/><rect x="15" y="16" width="4" height="8"/><rect x="21" y="19" width="4" height="5"/><path d="M3 6l8 6 6-3 8 8" stroke="#fff" stroke-width="1.6" fill="none"/></svg></div>
    <h4>Reduced illness</h4>
    <p style="top:24px">Sed ut perspiciatis unde omnis iste natus erronsit voluptate cuol oeut perspiciatis undeomn isstnatusevo llatan.</p>
  </div>
  <div class="benefit" style="top:361px">
    <div class="benefit-icon"><svg width="28" height="28" viewBox="0 0 28 28" fill="#fff"><rect x="3" y="18" width="4" height="7"/><rect x="9" y="14" width="4" height="11"/><rect x="15" y="10" width="4" height="15"/><rect x="21" y="5" width="4" height="20"/></svg></div>
    <h4>Increased socialization with other children vs. Sole Nanny</h4>
    <p style="top:45px">Sed ut perspiciatis unde omnis iste natus erronsit voluptate cuol oeut perspiciatis undeomn isstnatusevo llatan.</p>
  </div>
</section>

<h2 class="section-title" style="top:2246px">FAQ</h2>
<div class="faq-item" style="left:162px;top:2317px">Lorem ipsum dolor sit amet, consectetu?<span class="plus">+</span></div>
<div class="faq-item" style="left:162px;top:2379px">Quisque venenatis neque quis orci feugiat temp?<span class="plus">+</span></div>
<div class="faq-item open" style="left:162px;top:2440px">Cras aliquet arcu vel ipsum sagittis dapibus?<span class="plus">−</span></div>
<div class="faq-answer">Sed ut perspiciatis unde omnis iste natus erronsit voluptate cuaol oeut perspiciatis unde omnisstnatusvoluptatemcustum dolor emque lau tumSed ut perspiciatis unde omnis iste natus error sit volup</div>
<div class="faq-item" style="left:609px;top:2317px">Proin sit amet dui id leo eleifend blandit?<span class="plus">+</span></div>
<div class="faq-item" style="left:609px;top:2379px">Lorem ipsum dolor sit amet, consectetu?<span class="plus">+</span></div>
<div class="faq-item" style="left:609px;top:2440px">Proin sit amet dui id leo eleifend blandit?<span class="plus">+</span></div>
<div class="faq-item" style="left:609px;top:2502px">Lorem ipsum dolor sit amet, consectetu?<span class="plus">+</span></div>
<div class="faq-item" style="left:609px;top:2563px">Lorem ipsum dolor sit amet, consectetu?<span class="plus">+</span></div>

<section class="newsletter">
  <h3>Newsletter Sign Up</h3>
  <div class="nl-input">Email Address</div>
  <a class="nl-submit">SIGNUP</a>
</section>

<footer class="site-footer">
  <div class="footer-brand">Bright Pram Hub</div>
  <p class="footer-about">Sed uterspiciatiserspiciatis unde ers piciatis undeed uerspiciatiem omnis teatuerspiciatierspi unde ed uerspiciatisit</p>
  <div class="footer-col" style="left:420px"><h5>About</h5><ul><li>Refer</li><li>Careers</li><li>News</li><li>Our nanny</li><li>Contact</li></ul></div>
  <div class="footer-col" style="left:560px"><h5>Services</h5><ul><li>Sed uterspiciatis</li><li>Perspiciatis unde</li><li>Perspiciatis unde</li><li>Sed uerspiciatiem</li><li>Comnisteatusit</li></ul></div>
  <div class="footer-col" style="left:738px"><h5>Who we are</h5><ul><li>Sed uterspiciatis</li><li>Perspiciatis unde</li><li>Perspiciatis unde</li><li>Sed uerspiciatiem</li><li>Comnisteatusit</li></ul></div>
  <div class="footer-col" style="left:927px"><h5>Other Links</h5><ul><li>Sed uterspiciatis</li><li>Perspiciatis unde</li><li>Perspiciatis unde</li><li>Sed uerspiciatiem</li><li>Comnisteatusit</li></ul></div>
  <div class="footer-rule"></div>
  <div class="social">
    <svg width="24" height="18" viewBox="0 0 24 18"><rect x="1" y="1" width="22" height="16" fill="#1d1d1d"/><path d="M1 1l11 9 11-9" stroke="#f1f1f1" stroke-width="1.6" fill="none"/></svg><span></span><span></span><span></span>
  </div>
  <div class="copyright">© 2018 Bright Pram Hub. Privacy Policy | Terms of Use | Contact</div>
</footer>

</body>
</html>
```